Business card design for my company.
I would like the card's background colour to be black. You can also see our web site to get an idea of our brand. https://www.tmwhomecrafting.com.au/
- Name
- Email

```html
<!DOCTYPE html>
<html lang="en">
<head>
<meta charset="utf-8">
<title>TMW Home Crafting – Business Card</title>
<link rel="stylesheet" href="https://fonts.googleapis.com/css2?family=Roboto:wght@400;500;700&display=swap">
<style>
  :root {
    --stage: #2b2b2d;
    --card: #232325;
    --green: #0f9a45;
    --white: #ffffff;
    --soft-white: #e6e6e6;
    --gloss: #141416;
  }
  * { box-sizing: border-box; margin: 0; padding: 0; }
  html, body {
    width: 1200px; height: 852px; overflow: hidden;
    background: var(--stage);
    font-family: "Roboto", Arial, sans-serif;
  }
  .stage { position: relative; width: 1200px; height: 852px; }
  .card {
    position: absolute; top: 266px;
    width: 560px; height: 320px;
    border-radius: 18px; overflow: hidden;
    background: var(--card);
    box-shadow: 0 14px 30px rgba(0,0,0,0.45);
  }
  .card--front { left: 30px; border-bottom: 8px solid var(--green); }
  .card--back { left: 610px; }

  /* Front */
  .brand-mark {
    position: absolute; left: 0; right: 0; top: 110px;
    display: flex; justify-content: center; align-items: center; gap: 14px;
  }
  .brand-mark__square { width: 34px; height: 34px; background: var(--gloss); flex: none; }
  .brand-mark__name {
    font-weight: 700; font-size: 34px; color: var(--gloss);
    letter-spacing: 1px; white-space: nowrap;
  }
  .front-url {
    position: absolute; right: 34px; bottom: 22px;
    font-size: 14px; color: var(--soft-white);
  }

  /* Back */
  .back-band { position: absolute; inset: 0; }
  .back-logo {
    position: absolute; left: 36px; top: 176px; width: 248px;
    display: flex; align-items: center; gap: 10px;
  }
  .back-logo__square { width: 24px; height: 24px; background: var(--white); flex: none; }
  .back-logo__name {
    font-weight: 700; font-size: 20px; color: var(--white);
    white-space: nowrap;
  }
  .contact { position: absolute; left: 300px; top: 38px; width: 240px; }
  .contact__name { font-weight: 500; font-size: 22px; color: var(--green); }
  .contact__role { font-size: 14px; color: var(--soft-white); margin-top: 2px; }
  .contact__list { list-style: none; margin-top: 22px; }
  .contact__item {
    display: flex; align-items: center; gap: 10px;
    font-size: 13.5px; color: var(--soft-white);
    line-height: 20px; white-space: nowrap;
  }
  .contact__item svg { width: 12px; height: 12px; fill: var(--green); flex: none; }
  .band-label {
    position: absolute; right: 34px; bottom: 52px;
    font-size: 14px; color: var(--white);
  }
</style>
</head>
<body>
<main class="stage">

  <section class="card card--front" aria-label="Card front">
    <div class="brand-mark">
      <span class="brand-mark__square"></span>
      <span class="brand-mark__name">TMW Home Crafting</span>
    </div>
    <p class="front-url">www.tmwhomecrafting.com.au</p>
  </section>

  <section class="card card--back" aria-label="Card back">
    <svg class="back-band" viewBox="0 0 560 320" preserveAspectRatio="none" aria-hidden="true">
      <polygon points="0,296 300,296 300,320 0,320" fill="#ffffff"/>
      <path d="M290,320 L300,258 Q304,236 326,236 L560,236 L560,320 Z" fill="#0f9a45"/>
    </svg>

    <div class="back-logo">
      <span class="back-logo__square"></span>
      <span class="back-logo__name">TMW Home Crafting</span>
    </div>

    <div class="contact">
      <h1 class="contact__name">Liam Harper</h1>
      <p class="contact__role">General Manager</p>
      <ul class="contact__list">
        <li class="contact__item">
          <svg viewBox="0 0 24 24"><path d="M6.6 10.8a15 15 0 0 0 6.6 6.6l2.2-2.2a1 1 0 0 1 1-.25 11.4 11.4 0 0 0 3.6.57 1 1 0 0 1 1 1V20a1 1 0 0 1-1 1A17 17 0 0 1 3 4a1 1 0 0 1 1-1h3.5a1 1 0 0 1 1 1c0 1.25.2 2.45.57 3.57a1 1 0 0 1-.25 1z"/></svg>
          0400 123 456
        </li>
        <li class="contact__item">
          <svg viewBox="0 0 24 24"><path d="M2 5h20v14H2z"/></svg>
          info@tmwhomecrafting.com.au
        </li>
        <li class="contact__item">
          <svg viewBox="0 0 24 24"><circle cx="12" cy="12" r="10"/></svg>
          www.tmwhomecrafting.com.au
        </li>
        <li class="contact__item">
          <svg viewBox="0 0 24 24"><path d="M12 2a7 7 0 0 0-7 7c0 5 7 13 7 13s7-8 7-13a7 7 0 0 0-7-7z"/></svg>
          Devonport, Tasmania, Australia
        </li>
      </ul>
    </div>

    <p class="band-label">TMW Home Crafting</p>
  </section>

</main>
</body>
</html>
```